Wordpress Design Project for Bankruptcy Law Office in San Francisco

our current website: www.dorvanelilaw-example.com

we would like to re-design it for wordpress to make it faster and a bit more modern.

content should be similar to what we have there right now but also we do family law

please include logo for law office:

Law Office of Marta K. Dolvenidze

Thank you.
Updates

please see attached word document with logos that we like as an example.

we do tend to like color red.  darker red.

Please submit your design variations and logo as soon as possible.   We would like to go over them and make our decision

Reason: Please create couple of more variations of logo for your design, so we can make our decision what we like the most. Please see word doc for samples: Text: Law Office Of Marta K. Dolvenidze

Reason: final touches

Target Market(s)

bankruptcy and family law clients

Industry/Entity Type

Family Law

Requirements
Must have
• see examples of law sites
http://promo.lexorbin-example.com/testimonials

- new logo: Law Office of Marta K. Dolvenidze
- client intake form
- blog
- contact us form

Nice to have
• - map
- red color
- on the front page a nice photo of SF or a happy family

```html
<!DOCTYPE html>
<html lang="en">
<head>
<meta charset="utf-8">
<title>Law Office of Marta K. Dolvenidze</title>
<link rel="stylesheet" href="https://fonts.googleapis.com/css2?family=Cinzel:wght@400&family=Roboto+Condensed:wght@400&family=PT+Sans:wght@400;700&family=Zilla+Slab:wght@700&family=Arimo:wght@400;700&display=swap">
<style>
:root{
  --bg:#ededed;
  --red-bright:#d30f1c;
  --nav:#4a0306;
  --box:#8e0f14;
  --text:#2a2a2a;
  --head-red:#b3141c;
  --link-yellow:#ffd700;
  --white:#ffffff;
}
*{margin:0;padding:0;box-sizing:border-box}
html,body{width:1096px;height:1200px;overflow:hidden}
body{background:var(--bg);font-family:"PT Sans",sans-serif;color:var(--text);position:relative}
.page{position:absolute;left:105px;top:18px;width:886px;height:1156px;background:var(--white);box-shadow:0 0 18px rgba(0,0,0,.35)}
.header{position:absolute;left:0;top:0;width:886px;height:99px;background:linear-gradient(180deg,#c0252b,#8d0d12)}
.brand-name{position:absolute;left:16px;top:22px;color:var(--white);font-family:"Cinzel",serif;font-weight:400}
.brand-name .pre{display:block;font-size:20px;line-height:24px}
.brand-name .main{display:block;font-size:31px;line-height:36px;letter-spacing:1px}
.phone{position:absolute;right:10px;top:56px;color:var(--white);font-family:"Cinzel",serif;font-size:25px;display:flex;align-items:center;gap:7px}
.phone svg{width:24px;height:24px}
.nav{position:absolute;left:0;top:99px;width:886px;height:41px;background:var(--nav)}
.nav a{position:absolute;top:10px;transform:translateX(-50%);color:var(--white);text-decoration:none;font-family:"Roboto Condensed",sans-serif;font-size:16px;white-space:nowrap}
.info-box{position:absolute;left:16px;top:159px;width:223px;height:254px;background:var(--box);color:var(--white)}
.info-box h3{position:absolute;left:15px;top:12px;font-weight:400;font-size:15px}
.info-box .sub{position:absolute;left:15px;top:49px;font-size:15px}
.info-box .photo{position:absolute;left:15px;top:71px;width:190px;height:77px;background:linear-gradient(90deg,#b53a3a,#e8d3b8,#f2d9d6);border:1px solid #fff}
.info-box p{position:absolute;left:17px;top:155px;width:190px;font-family:Arimo,sans-serif;font-size:10px;line-height:13.7px;text-align:justify}
.clip{position:absolute;width:12px;height:38px}
.banner{position:absolute;left:255px;top:159px;width:615px;height:254px;background:radial-gradient(circle at 70% 45%,#e39a2a 0,#b8881f 12%,#6b8d2a 30%,#8fb33c 55%,#4f7a22 100%)}
.banner h2{position:absolute;left:40px;top:14px;width:220px;text-align:center;color:var(--white);font-family:"Zilla Slab",serif;font-size:42px;line-height:55px;text-shadow:1px 2px 3px rgba(0,0,0,.45)}
.form-box{position:absolute;left:16px;top:434px;width:223px;height:305px;background:var(--box);border:2px dotted #c9c9c9;color:var(--white)}
.form-box h3{position:absolute;left:13px;top:10px;font-size:15px;font-weight:700}
.form-box .note{position:absolute;left:21px;top:52px;font-size:12.5px}
.field{position:absolute;left:13px;width:187px;height:23px;background:linear-gradient(#fafafa,#cfcfcf);border-radius:3px;color:#222;font-size:12px;padding:4px 8px}
.field.msg{height:64px}
.submit{position:absolute;left:139px;top:281px;width:60px;height:22px;background:#000;color:#fff;font-size:12px;text-align:center;line-height:22px}
.welcome{position:absolute;left:256px;top:430px;width:607px}
.welcome h1{font-size:18px;color:var(--head-red);font-weight:700;margin-bottom:6px;margin-left:-2px}
.welcome h2{font-size:16px;color:var(--head-red);font-weight:700;margin-top:11px}
.welcome p{font-size:12.6px;line-height:20px;text-align:justify}
.welcome p + p{margin-top:20px}
.card{position:absolute;top:762px;width:272px;height:222px;background:linear-gradient(160deg,var(--red-bright),#a70a12);border-radius:6px;color:var(--white);box-shadow:0 8px 8px -4px rgba(0,0,0,.45)}
.card h3{position:absolute;left:20px;top:18px;font-size:24px;font-weight:400;white-space:nowrap}
.card .photo{position:absolute;left:20px;top:51px;width:232px;height:57px}
.card p{position:absolute;left:18px;top:116px;width:236px;font-family:Arimo,sans-serif;font-size:11px;line-height:14.6px;text-align:justify}
.card .more{position:absolute;right:11px;top:200px;font-family:Arimo,sans-serif;font-size:11px;font-weight:700;color:var(--link-yellow)}
.footer{position:absolute;left:0;top:1025px;width:886px;height:131px;background:linear-gradient(180deg,#a3141a,#7f0a0f);color:var(--white);font-family:Arimo,sans-serif;font-size:11px}
.footer .meta{position:absolute;left:20px;top:17px}
.footer .meta span{margin-right:10px}
.footer .disclaimer{position:absolute;left:20px;top:53px;width:615px;line-height:16.5px}
.badge{position:absolute;left:771px;top:27px;width:93px;height:74px;background:#fff;box-shadow:8px 8px 0 rgba(255,255,255,.25)}
</style>
</head>
<body>
<div class="page">
  <header class="header">
    <div class="brand-name"><span class="pre">Law Office of</span><span class="main">Marta K. Dolvenidze</span></div>
    <div class="phone">
      <svg viewBox="0 0 24 24"><rect width="24" height="24" rx="4" fill="#fff"/><path d="M8 5c-1 0-2 1-2 3 0 5 5 11 10 11 2 0 3-1 3-2l-3-3-2 1c-2-1-4-3-5-5l1-2z" fill="#8d0d12"/></svg>
      415-555-0182
    </div>
  </header>
  <nav class="nav">
    <a style="left:89px">HOME</a>
    <a style="left:198px">ABOUT US</a>
    <a style="left:337px">AREAS OF PRACTICE</a>
    <a style="left:479px">RESOURCES</a>
    <a style="left:586px">BLOG</a>
    <a style="left:669px">FAQ</a>
    <a style="left:767px">CONTACT US</a>
  </nav>

  <aside class="info-box">
    <h3>IMPORTANT INFORMATION</h3>
    <div class="sub">chapter 7</div>
    <div class="photo" role="img" aria-label="Photo of a smiling family with children on bicycles"></div>
    <p>Often called the liquidation chapter, or “fresh start,” chapter 7 is used by individuals, families, partnerships, or corporations whose financial difficulties do not allow them to repay all of their debts.</p>
  </aside>
  <svg class="clip" style="left:234px;top:144px" viewBox="0 0 12 38"><rect x="2" y="1" width="8" height="36" rx="4" fill="none" stroke="#999" stroke-width="1.5"/></svg>

  <section class="banner" role="img" aria-label="Photo of an orange butterfly on white flowers against a green background">
    <h2>Always Protecting Client’s Interests!</h2>
  </section>

  <section class="form-box">
    <h3>CONTACT FORM</h3>
    <div class="note">Fields marked with * are required.</div>
    <div class="field" style="top:77px">Name *</div>
    <div class="field" style="top:110px">Email *</div>
    <div class="field" style="top:143px">Phone</div>
    <div class="field" style="top:176px">Subject *</div>
    <div class="field msg" style="top:209px">Message *</div>
    <div class="submit">SUBMIT</div>
  </section>

  <section class="welcome">
    <h1>Welcome to Debt Help Desk - Complete Bankruptcy Information</h1>
    <p>Gravel_-_main_pageThe Law Offices of Marta K. Dolvenidze is a consumer law office dedicated to consumer protection and zealously defending the rights of our clients. We offer the big firm quality legal representation with a small firm individualized attention to each client.</p>
    <p>Our office offers services in: all types of consumer bankruptcy filings, i.e. Chapter 7, Chapter 13, Chapter 11, negotiating a settlement of your debts, assisting you in the defense of collection litigation and defending you against foreclosure. Please review our site and see what we may be able to offer you. Feel free to call us at (415) 555-0182 or use our free case evaluation form.</p>
    <h2>Speak to a Lawyer</h2>
    <p style="margin-top:0">Unlike some other law firms, when you call the Law Office of Marta K. Dolvenidze you will speak to an actual attorney. Not a paralegal or assistant. And even after retaining our office you will still speak to an attorney unlike other firms where you cannot get a hold of your attorney after several attempts.</p>
  </section>

  <article class="card" style="left:17px">
    <h3>Debt Relief</h3>
    <div class="photo" role="img" aria-label="Photo of an attorney meeting with a couple" style="background:linear-gradient(90deg,#3b3a3e,#d9d3cb,#a5826a)"></div>
    <p>This page is available, however, but because occasionally circumstances occur in which toil and pain can procure him some great. To take a trivial example, which of us ever undertakes laborious physical exercise, except to obtain some advantage from it.</p>
    <span class="more">read more...</span>
  </article>
  <svg class="clip" style="left:279px;top:749px" viewBox="0 0 12 38"><rect x="2" y="1" width="8" height="36" rx="4" fill="none" stroke="#999" stroke-width="1.5"/></svg>

  <article class="card" style="left:307px">
    <h3 style="left:18px">Foreclosure Prevention</h3>
    <div class="photo" role="img" aria-label="Photo of a happy family in a car" style="background:linear-gradient(90deg,#6b6f75,#d9b79c,#8a8f96)"></div>
    <p>This page is available, however, but because occasionally circumstances occur in which toil and pain can procure him some great. To take a trivial example, which of us ever undertakes laborious physical exercise, except to obtain some advantage from it.</p>
    <span class="more">read more...</span>
  </article>
  <svg class="clip" style="left:568px;top:749px" viewBox="0 0 12 38"><rect x="2" y="1" width="8" height="36" rx="4" fill="none" stroke="#999" stroke-width="1.5"/></svg>

  <article class="card" style="left:595px">
    <h3>Chapter 13</h3>
    <div class="photo" role="img" aria-label="Photo of a relaxed smiling couple" style="background:linear-gradient(90deg,#e8e2dc,#c99f86,#eeeae6)"></div>
    <p>This page is available, however, but because occasionally circumstances occur in which toil and pain can procure him some great. To take a trivial example, which of us ever undertakes laborious physical exercise, except to obtain some advantage from it.</p>
    <span class="more">read more...</span>
  </article>
  <svg class="clip" style="left:856px;top:749px" viewBox="0 0 12 38"><rect x="2" y="1" width="8" height="36" rx="4" fill="none" stroke="#999" stroke-width="1.5"/></svg>

  <footer class="footer">
    <div class="meta"><span>Go to top</span> Copyright © 2010 KDLaw Group. All Rights Reserved. | Web Development by Webfernia | Design by RNQ Studio</div>
    <p class="disclaimer">Disclaimer: The Law Offices of Marta K. Dolvenidze is a Debt Relief law firm as defined by 11 U.S.C. 528. We help people file for Bankruptcy Relief under the Bankruptcy Code. The information contained on this website is not to be construed as legal advice. It is not intended to solicit or form an attorney-client relationship. We do not guarantee any result and prior results do not guarantee a similar outcome. This is an attorney advertisement and this website is for informational purposes only.</p>
    <div class="badge" role="img" aria-label="Professional association membership badge"></div>
  </footer>
</div>
</body>
</html>
```